Werbebrief
Zielgruppe
Unsere Zielgruppe sind Geschäftsführer junger Unternehmen.
Hallo,
Wir benötigen einen "Werbebrief". Es ist jedoch weniger ein Brief, als viel mehr eine etwas größerer "Werbekarte" (diese soll 105 x 210mm groß sein).
Auf der Vorderseite soll folgender Text stehen:
Für Unternehmen, die gerne expandieren möchten
Auf der Rückseite soll folgender Link stehen:
www.feldrok-studio.de/Expandieren
Darunter soll folgendes stehen:
Ihr persönlicher Code: ABC123
Wichtig ist, dass wir den Code individuell ändern können, da jeder einen anderen Code bekommt.
Unser Logo und Corporate Farbe habe ich hochgeladen. Das Design sollte auf jeden Fall zu unserer Webseite passen (www.feldrok-studio.de)
Wir freuen uns auf Ihre Vorschläge.

```html
<!DOCTYPE html>
<html lang="de">
<head>
<meta charset="utf-8">
<title>Tervolk – Werbekarten</title>
<link rel="stylesheet" href="https://fonts.googleapis.com/css2?family=Open+Sans:wght@400&display=swap">
<style>
  :root {
    --page-bg: #e9e6e1;
    --card-blue-light: #2a5aa6;
    --card-blue: #1f4c94;
    --card-blue-dark: #1a4183;
    --card-text: #ffffff;
    --divider: rgba(255, 255, 255, 0.55);
    --code-field: #f2f2f2;
  }
  * { box-sizing: border-box; margin: 0; padding: 0; }
  html, body {
    width: 1200px;
    height: 1200px;
    overflow: hidden;
  }
  body {
    background: var(--page-bg);
    font-family: "Open Sans", sans-serif;
    color: var(--card-text);
    display: flex;
    align-items: center;
    justify-content: center;
    gap: 60px;
  }
  .sheet {
    width: 500px;
    height: 750px;
    display: flex;
    flex-direction: column;
    box-shadow: 0 8px 24px rgba(0, 0, 0, 0.18);
  }
  .card {
    position: relative;
    height: 250px;
    background: radial-gradient(ellipse at 35% 30%, var(--card-blue-light) 0%, var(--card-blue) 55%, var(--card-blue-dark) 100%);
    display: flex;
    flex-direction: column;
    align-items: center;
    justify-content: center;
    text-align: center;
  }
  .card + .card { border-top: 1px solid var(--divider); }
  .brand {
    position: absolute;
    top: 18px;
    right: 24px;
    display: flex;
    align-items: center;
    gap: 8px;
    font-size: 21px;
    line-height: 1;
  }
  .brand-dot {
    width: 12px;
    height: 12px;
    border-radius: 50%;
    background: var(--card-text);
  }
  .front-claim {
    font-size: 22px;
    line-height: 1.4;
    margin-top: 20px;
  }
  .back-info {
    font-size: 21px;
    line-height: 1.35;
    margin-top: 24px;
  }
  .code-line {
    display: flex;
    align-items: center;
    justify-content: center;
    gap: 4px;
  }
  .code-field {
    display: inline-block;
    width: 110px;
    height: 26px;
    background: var(--code-field);
    color: var(--card-blue-dark);
    font-size: 17px;
    line-height: 26px;
  }
</style>
</head>
<body>
  <section class="sheet sheet-front" aria-label="Vorderseiten">
    <article class="card card-front">
      <div class="brand"><span class="brand-dot"></span><span class="brand-name">Tervolk</span></div>
      <p class="front-claim">Für Unternehmen, die gerne<br>expandieren möchten</p>
    </article>
    <article class="card card-front">
      <div class="brand"><span class="brand-dot"></span><span class="brand-name">Tervolk</span></div>
      <p class="front-claim">Für Unternehmen, die gerne<br>expandieren möchten</p>
    </article>
    <article class="card card-front">
      <div class="brand"><span class="brand-dot"></span><span class="brand-name">Tervolk</span></div>
      <p class="front-claim">Für Unternehmen, die gerne<br>expandieren möchten</p>
    </article>
  </section>

  <section class="sheet sheet-back" aria-label="Rückseiten">
    <article class="card card-back">
      <div class="brand"><span class="brand-dot"></span><span class="brand-name">Tervolk</span></div>
      <div class="back-info">
        <p class="link">www.feldrok-studio.de/Expandieren</p>
        <p class="code-line">Ihr persönlicher Code: <span class="code-field"></span></p>
      </div>
    </article>
    <article class="card card-back">
      <div class="brand"><span class="brand-dot"></span><span class="brand-name">Tervolk</span></div>
      <div class="back-info">
        <p class="link">www.feldrok-studio.de/Expandieren</p>
        <p class="code-line">Ihr persönlicher Code: <span class="code-field"></span></p>
      </div>
    </article>
    <article class="card card-back">
      <div class="brand"><span class="brand-dot"></span><span class="brand-name">Tervolk</span></div>
      <div class="back-info">
        <p class="link">www.feldrok-studio.de/Expandieren</p>
        <p class="code-line">Ihr persönlicher Code: <span class="code-field"></span></p>
      </div>
    </article>
  </section>
</body>
</html>
```